Business Card Design

Business Card for professional consulting firm working with large financial institutions.

Target Market(s)

Executive buyers

Industry/Entity Type

Banking

Contact Information for Business Card

Mild creativity wanted. Not boring, but do elaborate artwork.

Font styles to use
Serif
Sans Serif

Colors

Designer to choose colors to be used in the design.

Requirements
Must have
• Standard business card features - company name, individual name, telephone, website, email, locations.
Nice to have
• Two colors
Should not have
• too many colors, fancy printing, cartoons.

```html
<!DOCTYPE html>
<html lang="en">
<head>
<meta charset="utf-8">
<title>Halden Advisory – Business Card</title>
<link rel="stylesheet" href="https://fonts.googleapis.com/css2?family=Noto+Serif:wght@400&family=Roboto:wght@400;500&display=swap">
<style>
  :root {
    --backdrop: #dcdcdc;
    --card-white: #f4f4f4;
    --card-black: #1a1b1c;
    --ink: #222222;
    --ink-soft: #4a4a4a;
    --muted: #9a9a9a;
    --band-grey: #a7a7a7;
    --divider: #bdbdbd;
    --paper-white: #ffffff;
  }
  * { margin: 0; padding: 0; box-sizing: border-box; }
  html, body { width: 1200px; height: 960px; overflow: hidden; }
  body { background: var(--backdrop); position: relative; font-family: "Roboto", Arial, sans-serif; }

  .card { position: absolute; width: 600px; height: 343px; overflow: hidden; }
  .card--front { left: 314px; top: 113px; background: var(--card-white); }
  .card--back { left: 311px; top: 472px; background: var(--card-black); }

  .wordmark {
    position: absolute; left: 60px; top: 140px;
    font-family: "Noto Serif", Georgia, serif; font-size: 25px; color: var(--ink-soft);
    display: flex; align-items: center; gap: 10px;
  }
  .wordmark__dot { width: 12px; height: 12px; border-radius: 50%; background: var(--band-grey); }

  .divider { position: absolute; left: 331px; top: 86px; width: 1px; height: 154px; background: var(--divider); }

  .contact { position: absolute; left: 358px; top: 88px; color: var(--ink-soft); font-size: 14px; line-height: 18px; }
  .contact__name { font-family: "Noto Serif", Georgia, serif; font-size: 21px; line-height: 26px; color: var(--ink); letter-spacing: 0.5px; }
  .contact__role { font-size: 14px; color: var(--muted); font-weight: 500; line-height: 16px; }
  .contact__address { margin-top: 14px; }
  .contact__lines { margin-top: 11px; }
  .contact__line { display: flex; align-items: center; gap: 7px; }
  .contact__line svg { width: 13px; height: 13px; fill: var(--ink); }

  .footer-band { position: absolute; left: 0; bottom: 0; width: 600px; height: 42px; }
  .footer-band__url {
    position: absolute; right: 37px; bottom: 13px; color: var(--paper-white);
    font-size: 14px; letter-spacing: 1.4px;
  }

  .back-name {
    position: absolute; left: 312px; top: 144px;
    font-family: "Noto Serif", Georgia, serif; font-size: 42px; color: var(--paper-white);
  }
</style>
</head>
<body>
  <section class="card card--front">
    <div class="wordmark"><span class="wordmark__dot"></span>Halden Advisory</div>
    <div class="divider"></div>
    <div class="contact">
      <div class="contact__name">DANIEL REYES</div>
      <div class="contact__role">CEO/FOUNDER</div>
      <div class="contact__address">4120 Birchwood Court<br>Juneau, Alaska 34518</div>
      <div class="contact__lines">
        <div class="contact__line">
          <svg viewBox="0 0 24 24" aria-hidden="true"><path d="M6.6 10.8a15.1 15.1 0 0 0 6.6 6.6l2.2-2.2c.3-.3.7-.4 1-.2 1.1.4 2.3.6 3.6.6.6 0 1 .4 1 1V20c0 .6-.4 1-1 1A17 17 0 0 1 3 4c0-.6.4-1 1-1h3.5c.6 0 1 .4 1 1 0 1.3.2 2.5.6 3.6.1.3 0 .7-.2 1z"/></svg>
          <span>689 555 0142</span>
        </div>
        <div class="contact__line">
          <svg viewBox="0 0 24 24" aria-hidden="true"><path d="M2 5h20v14H2z M3 6l9 7 9-7" fill="none" stroke="#222" stroke-width="0"/><path d="M2 5h20L12 12z"/><path d="M2 7l10 7 10-7v12H2z"/></svg>
          <span>info@haldenadvisory.com</span>
        </div>
      </div>
    </div>
    <svg class="footer-band" viewBox="0 0 600 42" aria-hidden="true">
      <rect x="0" y="24" width="340" height="18" fill="#a7a7a7"/>
      <path d="M326 42 C334 12 350 0 380 0 H600 V42 Z" fill="#ffffff"/>
      <path d="M330 42 C338 14 353 2 382 2 H600 V42 Z" fill="#000000"/>
    </svg>
    <span class="footer-band__url">www.haldenadvisory.com</span>
  </section>

  <section class="card card--back">
    <div class="back-name">Halden Advisory</div>
  </section>
</body>
</html>
```